Verodex business card

Business card for sustainable investment company called "Verodex". Verodex is an exchange platform selling carbon credits between buyers and sellers. Carbon Credits are an environmental commodity for reducing global carbon emissions.

the card should obviously have our logo and the theme should be sustainability/environment mixed with a trading platform.

Contact Information for Business Card

Logo, Name, Title, Phone, Email

Colors
0054AA
0677BA
7BADD7
CADEEF
E8F1F8
0094D4
00A9DD
6FCCEA
C7EBF8
E9F6FB
00AB8E
00BBA5
67D7C9
C6EFE9
E9F9F6
59FF00
82FF00
B8FF75
E3FFCB
F4FFEA

```html
<!DOCTYPE html>
<html lang="en">
<head>
<meta charset="utf-8">
<title>Verodex business card</title>
<link rel="stylesheet" href="https://fonts.googleapis.com/css2?family=Montserrat:wght@400;500;600;700&display=swap">
<style>
  :root {
    --stage: #e9ecef;
    --paper: #ffffff;
    --navy: #1c2b4a;
    --ink: #2b3340;
    --sky: #2ea8e2;
    --blue: #0677ba;
    --band-start: #3fb3e8;
    --band-end: #4a7bd0;
    --back-start: #3a66c9;
    --back-end: #5cc3e8;
    --white: #ffffff;
  }
  * { box-sizing: border-box; margin: 0; padding: 0; }
  html, body {
    width: 1200px; height: 786px; overflow: hidden;
    background: var(--stage);
    font-family: "Montserrat", sans-serif;
  }
  .canvas {
    position: relative; width: 1200px; height: 786px;
  }
  .card {
    position: absolute; top: 238px;
    width: 540px; height: 309px;
    border-radius: 4px; overflow: hidden;
    box-shadow: 0 10px 28px rgba(20, 30, 50, 0.18);
  }
  .card-front { left: 40px; background: var(--paper); }
  .card-back { left: 620px; }

  /* front */
  .brand {
    position: absolute; left: 42px; top: 62px;
    display: flex; align-items: center; gap: 18px;
  }
  .brand-square {
    width: 58px; height: 58px; background: var(--sky);
  }
  .brand-name {
    font-size: 54px; font-weight: 700; letter-spacing: 1px;
    color: var(--navy); line-height: 1;
  }
  .person {
    position: absolute; left: 42px; top: 152px; width: 170px;
    text-align: right;
  }
  .person-name {
    font-size: 20px; font-weight: 700; color: var(--sky); line-height: 1.1;
  }
  .person-title {
    font-size: 12px; font-weight: 500; color: var(--ink); margin-top: 2px;
  }
  .divider {
    position: absolute; left: 232px; top: 146px;
    width: 1px; height: 58px; background: var(--sky);
  }
  .contacts {
    position: absolute; left: 252px; top: 144px;
    list-style: none;
  }
  .contacts li {
    display: flex; align-items: center; gap: 8px;
    font-size: 12.5px; font-weight: 500; color: var(--ink);
    line-height: 20px;
  }
  .contacts svg { width: 11px; height: 11px; fill: var(--sky); flex: none; }
  .address-band {
    position: absolute; left: 0; top: 226px;
    width: 100%; height: 38px;
    background: linear-gradient(90deg, var(--band-start), var(--band-end));
    display: flex; align-items: center; justify-content: space-between;
    padding: 0 26px 0 42px;
  }
  .address {
    font-size: 13px; font-weight: 500; color: var(--white);
  }
  .band-mark {
    width: 20px; height: 20px; border-radius: 50%;
    background: var(--white);
  }

  /* back */
  .back-field {
    position: absolute; inset: 0;
    background: linear-gradient(200deg, var(--back-end) 0%, var(--back-start) 100%);
  }
  .back-brand {
    position: absolute; right: 34px; bottom: 92px;
    display: flex; align-items: center; gap: 12px;
  }
  .back-brand .brand-square {
    width: 32px; height: 32px; background: var(--white);
  }
  .back-brand .brand-name {
    font-size: 28px; font-weight: 600; color: var(--white); letter-spacing: 1px;
  }
</style>
</head>
<body>
<main class="canvas">
  <section class="card card-front">
    <div class="brand">
      <span class="brand-square"></span>
      <span class="brand-name">VERODEX</span>
    </div>
    <div class="person">
      <p class="person-name">Jordan Ellis</p>
      <p class="person-title">CEO &amp; Founder</p>
    </div>
    <span class="divider"></span>
    <ul class="contacts">
      <li>
        <svg viewBox="0 0 24 24" aria-hidden="true"><path d="M6.6 10.8a15.1 15.1 0 0 0 6.6 6.6l2.2-2.2a1 1 0 0 1 1-.25 11.4 11.4 0 0 0 3.6.57 1 1 0 0 1 1 1V20a1 1 0 0 1-1 1A17 17 0 0 1 3 4a1 1 0 0 1 1-1h3.5a1 1 0 0 1 1 1c0 1.25.2 2.45.57 3.57a1 1 0 0 1-.25 1z"/></svg>
        (37) 555-0182
      </li>
      <li>
        <svg viewBox="0 0 24 24" aria-hidden="true"><path d="M2 5h20v14H2zM4 7v.5l8 5 8-5V7l-8 5z"/></svg>
        info@verodex.com
      </li>
      <li>
        <svg viewBox="0 0 24 24" aria-hidden="true"><path d="M12 2a10 10 0 1 0 0 20 10 10 0 0 0 0-20zm6.9 6h-3a15.6 15.6 0 0 0-1.3-3.9A8 8 0 0 1 18.9 8zM12 4c.8 1.2 1.5 2.5 1.9 4h-3.8c.4-1.5 1.1-2.8 1.9-4zM4.3 14a8 8 0 0 1 0-4h3.4a16 16 0 0 0 0 4zm.8 2h3a15.6 15.6 0 0 0 1.3 3.9A8 8 0 0 1 5.1 16zm3-8h-3a8 8 0 0 1 4.3-3.9A15.6 15.6 0 0 0 8.1 8zM12 20c-.8-1.2-1.5-2.5-1.9-4h3.8c-.4 1.5-1.1 2.8-1.9 4zm2.3-6H9.7a14.7 14.7 0 0 1 0-4h4.6a14.7 14.7 0 0 1 0 4zm.3 5.9a15.6 15.6 0 0 0 1.3-3.9h3a8 8 0 0 1-4.3 3.9zm1.7-5.9a16 16 0 0 0 0-4h3.4a8 8 0 0 1 0 4z"/></svg>
        www.verodex.com
      </li>
    </ul>
    <div class="address-band">
      <p class="address">48 Meridian Way, Suite 210, Halden, PA 19020</p>
      <span class="band-mark"></span>
    </div>
  </section>

  <section class="card card-back">
    <div class="back-field" role="img" aria-label="Blue gradient field with a repeating faint brand-mark pattern"></div>
    <div class="back-brand">
      <span class="brand-square"></span>
      <span class="brand-name">VERODEX</span>
    </div>
  </section>
</main>
</body>
</html>
```